Real Estate agent needs flyer/folder to contain bio and overview of services

I'm including files of the layout of the small folder. The folder is 6 1/2 across and 9 1/2 inches long. It will have a front & back cover and then writing on the 2 inside pages.

I am sending a few files to incorporate into the flyer, 1 new logo to use and 2 files which are coloring ideas.

Colors

Designer to choose colors to be used in the design.

```html
<!DOCTYPE html>
<html lang="en">
<head>
<meta charset="utf-8">
<title>Dana Whitfield – Realtor Folder</title>
<link href="https://fonts.googleapis.com/css2?family=Open+Sans:ital,wght@0,400;0,600;1,400&family=EB+Garamond:ital,wght@1,400;1,600&display=swap" rel="stylesheet">
<style>
  :root{
    --bg:#4d4d4d;
    --paper:#ffffff;
    --paper-shade:#e4e4e4;
    --blue-deep:#1d3f8f;
    --blue:#1a6fbf;
    --blue-mid:#2a86cf;
    --blue-light:#3fa0dc;
    --ink:#2a2a2a;
    --ink-soft:#444;
    --white:#ffffff;
  }
  *{box-sizing:border-box;margin:0;padding:0}
  html,body{width:1200px;height:1200px;overflow:hidden;background:var(--bg)}
  body{font-family:"Open Sans",Arial,sans-serif;color:var(--ink);position:relative}

  .spread{position:absolute;left:215px;width:770px;height:563px;display:flex;box-shadow:0 6px 18px rgba(0,0,0,.35)}
  .spread--outside{top:24px}
  .spread--inside{top:613px}
  .panel{position:relative;width:385px;height:563px;overflow:hidden}

  /* Back cover */
  .back-cover{background:linear-gradient(90deg,var(--paper) 0%,var(--paper-shade) 100%)}
  .brand{position:absolute;top:78px;left:0;width:100%;display:flex;align-items:center;justify-content:center;gap:7px}
  .brand__dot{width:14px;height:14px;border-radius:50%;background:var(--blue-deep)}
  .brand__name{font-size:13px;font-weight:600;color:var(--blue-deep);letter-spacing:.5px}
  .closing-note{position:absolute;top:258px;left:34px;width:317px;text-align:center;font-style:italic;font-size:11px;line-height:1.45;color:var(--ink-soft)}
  .agent{position:absolute;top:438px;left:0;width:100%;text-align:center}
  .agent__name{font-size:15px;color:var(--ink);margin-bottom:12px}
  .agent__line{font-size:9.5px;line-height:1.35;color:var(--ink-soft);display:flex;align-items:center;justify-content:center;gap:4px}
  .agent__line svg{width:9px;height:9px}
  .back-wave{position:absolute;left:0;bottom:0;width:385px;height:110px}

  /* Front cover */
  .front-cover{background:linear-gradient(90deg,var(--paper) 0%,#f1f1f1 100%)}
  .front-art{position:absolute;inset:0;width:385px;height:563px}
  .cover-logo{position:absolute;top:48px;left:12px;display:flex;align-items:center;gap:5px;z-index:1}
  .cover-logo__mark{width:9px;height:9px;background:var(--blue-deep);flex:none}
  .cover-logo__name{font-size:12px;font-weight:600;line-height:1.2;color:var(--blue-deep);text-align:center}

  /* Inside left */
  .intro{background:linear-gradient(180deg,var(--blue-mid) 0%,var(--blue) 60%,#1a6ab5 100%);color:var(--white)}
  .intro__building{position:absolute;left:0;top:0;width:140px;height:563px;background:linear-gradient(90deg,#9fbfd8 0%,#5d93c4 55%,rgba(42,134,207,0) 100%)}
  .intro__content{position:absolute;left:150px;top:0;width:228px;text-align:center}
  .intro h2{font-weight:400;font-size:15px;line-height:1.25}
  .intro__title{margin-top:26px}
  .portrait{width:104px;height:104px;border-radius:50%;margin:18px auto 10px;background:radial-gradient(circle at 50% 45%,#d9b48e 0%,#a8794f 55%,#e9eef3 100%);border:2px solid rgba(255,255,255,.35)}
  .intro p{font-size:5.8px;line-height:1.4;margin-bottom:0}
  .intro__tenet{margin-top:18px;margin-bottom:10px}
  .intro__services{margin-top:20px;margin-bottom:10px}
  .intro .lead{margin-bottom:1px}

  /* Inside right */
  .services{background:linear-gradient(180deg,#f4f4f4 0%,#dcdcdc 70%)}
  .hero{position:absolute;top:0;left:0;width:385px;height:175px;background:linear-gradient(90deg,#eaeaea 0%,#e7cbb3 30%,#c7c9cc 55%,#d9b49a 75%,#efefef 100%)}
  .column{position:absolute;top:176px;width:165px}
  .column--sell{left:16px}
  .column--buy{left:197px}
  .column h3{font-weight:600;font-size:15px;color:var(--ink);margin-bottom:12px}
  .column p{font-size:5.8px;line-height:1.36;color:var(--ink-soft)}
  .column .gap{margin-top:6px}
  .testimonials{position:absolute;left:0;top:413px;width:385px;height:150px;background:linear-gradient(180deg,var(--blue) 0%,var(--blue-mid) 100%);color:var(--white)}
  .testimonials__head{position:absolute;top:12px;left:16px;display:flex;align-items:center;gap:6px}
  .testimonials__head span{font-size:11px}
  .testimonials__head svg{width:20px;height:18px}
  .quote{position:absolute;font-family:"EB Garamond",Georgia,serif;font-style:italic;font-size:6px;line-height:1.38}
  .quote cite{display:block;text-align:right;font-style:normal;font-weight:600;margin-top:3px}
  .quote--one{left:16px;top:42px;width:168px}
  .quote--two{left:198px;top:20px;width:168px}
  .quote--three{left:198px;top:78px;width:168px}
</style>
</head>
<body>

<section class="spread spread--outside">
  <div class="panel back-cover">
    <div class="brand"><span class="brand__dot"></span><span class="brand__name">Harbor Crest Realty</span></div>
    <p class="closing-note">Along with being your Realtor, I'm a lifelong resource for all things home-related &amp; beyond...if you need a great referral for anything at all, call me! &nbsp;I can't wait to work with you!</p>
    <div class="agent">
      <p class="agent__name">Dana Whitfield</p>
      <p class="agent__line"><svg viewBox="0 0 10 10"><path d="M2 1l2 2-1 1.2c.6 1.2 1.6 2.2 2.8 2.8L7 6l2 2-1.2 1.5C4.5 9.3.7 5.5.5 2.2z" fill="var(--blue-deep)"/></svg>555 014 2290</p>
      <p class="agent__line"><svg viewBox="0 0 10 10"><rect x=".8" y="2" width="8.4" height="6" fill="none" stroke="var(--blue-deep)" stroke-width=".9"/><path d="M.8 2L5 5.5 9.2 2" fill="none" stroke="var(--blue-deep)" stroke-width=".9"/></svg>dana@whitfieldhomes.com</p>
      <p class="agent__line"><svg viewBox="0 0 10 10"><circle cx="5" cy="5" r="4" fill="var(--blue)"/><path d="M1 5h8M5 1c-2 2.5-2 5.5 0 8M5 1c2 2.5 2 5.5 0 8" stroke="#fff" stroke-width=".6" fill="none"/></svg>www.whitfieldhomes.com</p>
    </div>
    <svg class="back-wave" viewBox="0 0 385 110" preserveAspectRatio="none">
      <defs>
        <linearGradient id="waveBack" x1="0" y1="0" x2="1" y2="0">
          <stop offset="0" stop-color="#1e88d0"/><stop offset="1" stop-color="#1d3f8f"/>
        </linearGradient>
      </defs>
      <path d="M0 38 C30 18 70 20 110 45 C170 85 280 90 385 0 L385 110 L0 110 Z" fill="url(#waveBack)"/>
      <path d="M0 55 C40 40 80 48 120 68 C190 100 300 90 385 25 L385 110 L0 110 Z" fill="#2a9ad9" opacity=".55"/>
    </svg>
  </div>

  <div class="panel front-cover">
    <svg class="front-art" viewBox="0 0 385 563" role="img" aria-label="Photograph of a large stone two-storey house with a balcony, framed by a blue curve">
      <defs>
        <linearGradient id="housePhoto" x1="0" y1="0" x2="0" y2="1">
          <stop offset="0" stop-color="#4f93d6"/>
          <stop offset=".22" stop-color="#8ab8e2"/>
          <stop offset=".3" stop-color="#cfcbc3"/>
          <stop offset=".62" stop-color="#bdb6aa"/>
          <stop offset=".78" stop-color="#5f8a48"/>
          <stop offset="1" stop-color="#6f9e3e"/>
        </linearGradient>
        <linearGradient id="frameBlue" x1="0" y1="0" x2="1" y2="1">
          <stop offset="0" stop-color="#1d3f8f"/><stop offset="1" stop-color="#1a6fbf"/>
        </linearGradient>
      </defs>
      <path d="M138 0 C70 110 15 230 22 340 C30 450 170 520 385 470 L385 0 Z" fill="url(#frameBlue)"/>
      <path d="M160 0 C100 110 45 230 48 330 C52 430 190 490 385 455 L385 0 Z" fill="#2a86cf"/>
      <path d="M175 0 C120 110 62 230 62 325 C62 420 200 475 385 440 L385 0 Z" fill="url(#housePhoto)"/>
    </svg>
    <div class="cover-logo"><span class="cover-logo__mark"></span><span class="cover-logo__name">Dana<br>Whitfield</span></div>
  </div>
</section>

<section class="spread spread--inside">
  <div class="panel intro">
    <div class="intro__building" role="img" aria-label="Photograph of a modern apartment building with glass balconies"></div>
    <div class="intro__content">
      <h2 class="intro__title">Let me introduce myself</h2>
      <div class="portrait" role="img" aria-label="Portrait photograph of the agent"></div>
      <p>I'm originally from Chicago, but I'm a full-fledged California girl now. I've lived and worked in Orange County since 1996. I always say where we live is the next best thing to living on a tropical island. I've traveled to many and I'm always happy to come back to my Laguna Niguel home.</p>
      <p>My passion for this area is why I'm in Real Estate. I consider myself incredibly fortunate to sell homes and help people purchase homes in an area that I love with all my heart.</p>
      <p>This passion also carries over in representing my clients with the highest degree of professionalism, enthusiasm and care. My business is built on exceptional customer service and I'm grateful my clients are mostly repeat and referrals.</p>

      <h2 class="intro__tenet">My Core Tenet</h2>
      <p class="lead">It's All About YOU!</p>
      <p>My #1 priority is understanding YOUR needs and YOUR objectives. This understanding, along with working diligently on your behalf, means we accomplish your goal whether you're purchasing your first home or selling a home you've loved so you can move on to the next chapter of your life.</p>

      <h2 class="intro__services">Real Estate Services &amp;<br>Beyond...</h2>
      <p>Simply put, I help people who are local, relocating and investing, sell and purchase homes in Southern California. For purchases outside of California, I can refer to a network of agents across the country.</p>
      <p>I also provide a team who is dedicated to providing outstanding customer service throughout the transaction. My team includes a network of lenders, title, and escrow officers, in-house CPA, stagers, photographers, contractors and more.</p>
    </div>
  </div>

  <div class="panel services">
    <div class="hero" role="img" aria-label="Photograph of one hand holding house keys and another holding a small model house"></div>

    <div class="column column--sell">
      <h3>Selling your home</h3>
      <p>Selling your home is not like any other business transaction. It's also personal. My priority as your Listing Agent is to guide you through what can be a complicated and sometimes emotional process.</p>
      <p>I place great emphasis on marketing your property with professional photographs, along with harnessing the power of the Internet and the virtual world to reach as many buyers as possible. Your property will be marketed to the public as well as to other agents, thus creating maximum exposure of your home.</p>
      <p>When we first meet to discuss selling your home, it's essential for me to gain an understanding of your unique needs such as time lines, expectations and financial considerations, just to name a few. From there, I begin the process of listing and marketing your home. I lead you through negotiations and more paperwork than you ever care to do, guiding you to the successful closing of your home.</p>
    </div>

    <div class="column column--buy">
      <h3>Buying a home</h3>
      <p>If you're thinking about buying a home, it's imperative you have an accomplished, real estate professional by your side to walk you through what is likely the largest purchase of your life.</p>
      <p>To get started, I like to meet with you so we have an opportunity to get to know each other as purchasing a home is a uniquely personal endeavor. At that time, we can discuss your goals and if it's a good time for you to purchase a home.</p>
      <p class="gap">From there, the first step is to obtain a pre-approval from a lender. I'm able to recommend various lenders who can introduce and explain the various loan products available.</p>
      <p>After you've been pre-approved, that's when the fun starts! I guide you through the home buying adventure every step of the way and look forward to handing you the keys to your new home.</p>
    </div>

    <div class="testimonials">
      <div class="testimonials__head">
        <svg viewBox="0 0 20 18"><path d="M3 2h14a2 2 0 0 1 2 2v7a2 2 0 0 1-2 2H9l-4 4v-4H3a2 2 0 0 1-2-2V4a2 2 0 0 1 2-2z" fill="none" stroke="#fff" stroke-width="1"/><path d="M5 6h10M5 8.5h10M5 11h7" stroke="#fff" stroke-width=".8"/></svg>
        <span>Testimonials:</span>
      </div>
      <blockquote class="quote quote--one">During the home buying process, Dana becomes your trusted advisor, mentor and friend. Her knowledge of the industry, community and market are best in class. A true professional! Dana aligned her goals with my own and understood the motivation behind my purchase. Dana is unequivocally the reason why I was able to purchase my home in Laguna Niguel and provide my family with a world class community. Without her guidance and experience, I would still be in the market attempting to navigate the ever changing world of real estate.<cite>Marisol Vega</cite></blockquote>
      <blockquote class="quote quote--two">Dana got us an amazing deal on our new home and sold our old home in a week. Dana is patient, hardworking, professional and most importantly HONEST. Dana is definitely one of the best in the business!<cite>Priya &amp; Owen Hale</cite></blockquote>
      <blockquote class="quote quote--three">Dana is the kind of Real Estate professional everyone wants to represent them. She is knowledgeable, ethical, energetic, and follows up on every detail. Her honesty, integrity and expertise combined make her a very special and remarkable professional. We were lucky to find her!<cite>Gordon &amp; Ellen Ruiz</cite></blockquote>
    </div>
  </div>
</section>

</body>
</html>
```